Store Promo Card (already have logo!)

I need a card design (single side) for my online women’s gift shop containing a promotional code to be placed in bags for attendees at an event. I’m flexible on both shape and sizing, but perhaps a 4x6 card.
—It should contain my attached logo, my website (www.brivelhome.com), and my Instagram handle (@brivelhome) and promotion language such as “15% off your purchase with code: PELVON”.
—I think I would like my logo to be large.
—It should be clean, simple and modern in design and should use the colors from my logo.
—I would like about 3-5 product pictures depending on design.
Target Market(s)
Women ages 30 to 60
Industry/Entity Type
Retail Upscale Gift

```html
<!DOCTYPE html>
<html lang="en">
<head>
<meta charset="utf-8">
<title>Brivel Home – Promo Card</title>
<link rel="stylesheet" href="https://fonts.googleapis.com/css2?family=Abril+Fatface&family=Libre+Baskerville:wght@700&family=Montserrat:wght@500&display=swap">
<style>
  :root {
    --page: #ffffff;
    --blush: #ebd1cb;
    --ink: #626262;
  }
  * { margin: 0; padding: 0; box-sizing: border-box; }
  html, body {
    width: 1200px;
    height: 600px;
    overflow: hidden;
    background: var(--page);
  }
  .promo-card { display: block; width: 1200px; height: 600px; }
  .card-face { fill: var(--blush); }
  .frame { fill: none; stroke: var(--ink); stroke-width: 2.6; }
  .brand-name {
    font-family: "Abril Fatface", "Bodoni Moda", serif;
    font-size: 88px;
    letter-spacing: 2px;
    fill: var(--ink);
  }
  .brand-tag {
    font-family: "Montserrat", Arial, sans-serif;
    font-weight: 500;
    font-size: 21px;
    letter-spacing: 3px;
    fill: var(--ink);
  }
  .offer-figure {
    font-family: "Abril Fatface", "Bodoni Moda", serif;
    font-size: 148px;
    letter-spacing: 2px;
    fill: var(--ink);
  }
  .contact-web,
  .contact-handle,
  .offer-line,
  .offer-code {
    font-family: "Libre Baskerville", Georgia, serif;
    font-weight: 700;
    fill: var(--ink);
  }
  .contact-web { font-size: 39px; }
  .contact-handle { font-size: 28px; }
  .offer-line { font-size: 23px; }
  .offer-code { font-size: 36px; letter-spacing: 1px; }
  .handle-mark { fill: none; stroke: var(--ink); stroke-width: 2.6; }
</style>
</head>
<body>
<svg class="promo-card" viewBox="0 0 1200 600" xmlns="http://www.w3.org/2000/svg">
  <rect class="card-face" x="33" y="29" width="1134" height="542"/>

  <!-- brand block -->
  <g class="brand-block">
    <path class="frame" d="M304 260 H75 V69 H625 V260 H397"/>
    <text class="brand-name" x="350" y="200" text-anchor="middle">BRIVEL</text>
    <text class="brand-tag" x="351" y="268" text-anchor="middle">HOME</text>
  </g>

  <!-- contact block -->
  <g class="contact-block">
    <path class="frame" d="M187 529 H75 V337 H625 V529 H513"/>
    <text class="contact-web" x="350" y="444" text-anchor="middle">www.brivelhome.com</text>
    <rect class="handle-mark" x="214" y="506" width="26" height="26" rx="3"/>
    <text class="contact-handle" x="256" y="530">@brivelhome</text>
  </g>

  <!-- offer block -->
  <g class="offer-block">
    <path class="frame" d="M760 531 H657 V71 H1121 V531 H993"/>
    <text class="offer-figure" x="889" y="247" text-anchor="middle">15%</text>
    <text class="offer-figure" x="889" y="376" text-anchor="middle">OFF</text>
    <text class="offer-line" x="889" y="477" text-anchor="middle">your purchase with code:</text>
    <text class="offer-code" x="877" y="531" text-anchor="middle" dominant-baseline="middle">PELVON</text>
  </g>
</svg>
</body>
</html>
```